Lendquay wedsite and logo refresh

We are looking for someone to refresh the look and feel of Lendquay.co.nz we are moving it towards a more traditional brokerage.

Target Market(s)

30 to 55 year old professionals

Coding

Coded - Design and coding required

Number of Pages Required

3 page

Requirements
Nice to have
• we are needing a modern professional look

```html
<!DOCTYPE html>
<html lang="en">
<head>
<meta charset="utf-8">
<title>Lendquay — Find and compare rates</title>
<link rel="stylesheet" href="https://fonts.googleapis.com/css2?family=Oswald:wght@300;400;500&family=Montserrat:wght@400;500&display=swap">
<style>
:root{
  --orange:#f15a24;
  --grey-band:#58585a;
  --charcoal:#3d3d3f;
  --ink:#333333;
  --muted:#555555;
  --light:#f6f6f6;
  --white:#ffffff;
  --head:'Oswald',sans-serif;
  --body:'Montserrat',sans-serif;
}
*{box-sizing:border-box;margin:0;padding:0}
html,body{width:1200px;height:3750px;overflow:hidden}
body{position:relative;background:var(--white);font-family:var(--body);color:var(--ink)}
.abs{position:absolute}
.head{font-family:var(--head);font-weight:400;text-transform:uppercase}
.light{font-weight:300}

/* top bar & header */
.topbar{left:0;top:0;width:1200px;height:45px;background:var(--orange);color:var(--white)}
.topbar .welcome{left:172px;top:12px;font-size:15px;font-weight:300}
.lang-group{right:172px;top:12px;display:flex;align-items:center;gap:8px;font-family:var(--head);font-size:12px;font-weight:300}
.flag{display:block;width:32px;height:20px;margin-right:12px}
.flag:last-child{margin-right:0}
.header{left:0;top:45px;width:1200px;height:92px;background:var(--white);border-bottom:1px solid #ddd}
.brand{left:172px;top:18px;font-family:var(--head);font-size:40px;font-weight:300;color:var(--orange);letter-spacing:.5px}
.nav{left:506px;top:33px;display:flex;gap:16px;font-family:var(--head);font-weight:300;font-size:15px;text-transform:uppercase;color:var(--ink)}
.btn-login{left:708px;top:24px;width:86px;height:42px;background:var(--orange);color:var(--white);font-size:15px;line-height:42px;text-align:center}
.btn-signup{left:806px;top:24px;width:160px;height:42px;background:var(--grey-band);color:var(--white);font-size:15px;line-height:42px;text-align:center}
.menu{left:982px;top:24px;width:44px;height:42px;border:1px solid var(--ink)}

/* hero */
.hero{left:0;top:137px;width:1200px;height:760px;background:linear-gradient(90deg,#f5f5f5,#ececec)}
.hero-photo{left:470px;top:137px;width:730px;height:620px;background:linear-gradient(120deg,#e9e6e2 0%,#d4cbc6 45%,#7a5570 62%,#3c4a44 82%,#cfcac4 100%)}
.hero-title{left:170px;top:222px;font-size:60px;line-height:73px;font-weight:400;color:var(--orange);letter-spacing:-.5px}
.hero-btn{left:172px;top:466px;width:282px;height:61px;border:3px solid var(--orange);color:var(--orange);font-size:23px;font-weight:300;line-height:55px;text-align:center}
.hero-band{left:0;top:660px;width:1200px;height:237px}
.hero-intro{left:150px;top:750px;width:900px;text-align:center;color:var(--white);font-size:19px;font-weight:300;line-height:40px}
.round-btn{width:50px;height:50px;border-radius:50%;background:var(--white);border:2px solid var(--charcoal)}

/* why */
.why-title{left:0;top:975px;width:1200px;text-align:center;font-size:36px;font-weight:500;color:var(--orange)}
.why-sub{left:0;top:1032px;width:1200px;text-align:center;font-family:var(--head);font-weight:300;font-size:18px;color:var(--ink)}
.feature h3{font-family:var(--head);font-weight:300;font-size:18px;text-transform:uppercase;margin-bottom:10px}
.feature p{font-size:12.5px;line-height:19px;color:var(--muted)}
.feature.right{text-align:right}
.feature.left{text-align:justify}
.accent{color:var(--orange)}
.btn-solid{background:var(--orange);color:var(--white);font-family:var(--head);font-weight:300;text-transform:uppercase;text-align:center}

/* who */
.who{left:0;top:1718px;width:1200px;height:525px;background:var(--light)}
.who-photo{left:600px;top:1718px;width:600px;height:525px}
.who-title{left:172px;top:1800px;font-size:36px;font-weight:500;color:var(--orange)}
.who-sub{left:172px;top:1856px;font-family:var(--head);font-weight:300;font-size:18px}
.who-text{left:172px;top:1896px;width:398px;font-size:13.5px;line-height:25px;color:var(--muted);text-align:justify}
.who-quote{left:172px;top:2007px;width:398px;font-size:13.5px;line-height:22px;color:var(--orange);text-align:justify}

/* rates */
.rates-title{left:0;top:2335px;width:1200px;text-align:center;font-size:36px;font-weight:500;color:var(--orange)}
.tile{width:268px;height:226px;overflow:hidden}
.tile .label{position:absolute;left:0;bottom:30px;width:100%;text-align:center;color:var(--white);font-family:var(--head);font-weight:300;font-size:22px;text-transform:uppercase;white-space:nowrap}
.tile svg{position:absolute;left:94px;top:40px}

/* contact band & footer */
.contact-band{left:0;top:3036px;width:1200px;height:714px;background:var(--charcoal)}
.cta-row{left:0;top:3116px;width:1200px;display:flex;justify-content:center;align-items:center;gap:44px}
.cta-text{font-size:27px;font-weight:300;color:var(--white);white-space:nowrap}
.cta-btn{width:106px;height:44px;background:var(--white);color:var(--orange);font-family:var(--head);font-weight:300;font-size:16px;line-height:44px;text-align:center}
.foot-h{font-family:var(--head);font-weight:300;font-size:24px;color:var(--white);text-transform:uppercase}
.foot-links{font-size:13.5px;line-height:27px;color:var(--white)}
.field{border:1px solid var(--white);color:var(--white);font-size:13.5px;padding:12px 8px}
.rule{left:172px;top:3643px;width:856px;height:1px;background:#8a8a8a}
.copy{left:0;top:3688px;width:1200px;text-align:center;font-family:var(--head);font-weight:300;font-size:16px;color:var(--white)}
</style>
</head>
<body>

<!-- top bar -->
<div class="abs topbar">
  <div class="abs welcome head">Welcome to Lendquay!</div>
  <div class="abs lang-group">
    <span>ENGLISH</span><span class="flag" style="background:#2b3f8f"></span>
    <span>CHINESE</span><span class="flag" style="background:#e8281e"></span>
  </div>
</div>

<!-- header -->
<header class="abs header">
  <div class="abs brand">LENDQUAY</div>
  <nav class="abs nav"><span>Services</span><span>About</span><span>Contact</span></nav>
  <div class="abs btn-login head light">Login</div>
  <div class="abs btn-signup head light">Sign up for free</div>
  <div class="abs menu">
    <svg width="42" height="40" viewBox="0 0 42 40"><g stroke="#333" stroke-width="2"><line x1="10" y1="13" x2="32" y2="13"/><line x1="10" y1="20" x2="32" y2="20"/><line x1="10" y1="27" x2="32" y2="27"/></g></svg>
  </div>
</header>

<!-- hero -->
<section>
  <div class="abs hero"></div>
  <div class="abs hero-photo" role="img" aria-label="Photo of two smiling professionals reviewing documents at an office desk"></div>
  <h1 class="abs hero-title head">No oblivations<br>No fees<br>No worries</h1>
  <div class="abs hero-btn head">Find and compare rates</div>
  <svg class="abs hero-band" width="1200" height="237" viewBox="0 0 1200 237"><path d="M0 82 Q600 -40 1200 70 L1200 237 L0 237 Z" fill="#58585a"/></svg>
  <p class="abs hero-intro head">Lendquay is an online marketplace where you can quickly find &amp; compare great rates from leading mortgage, insurance and finance providers.</p>
  <div class="abs round-btn" style="left:573px;top:872px">
    <svg width="46" height="46" viewBox="0 0 46 46"><polyline points="14,19 23,28 32,19" fill="none" stroke="#3d3d3f" stroke-width="2.5"/></svg>
  </div>
</section>

<!-- why -->
<section>
  <h2 class="abs why-title head">Why Lendquay?</h2>
  <p class="abs why-sub">Our mission is to put the power in the hands of the consumer</p>

  <svg class="abs" style="left:380px;top:1090px" width="440" height="440" viewBox="0 0 440 440">
    <circle cx="218" cy="220" r="177" fill="none" stroke="#f15a24" stroke-width="42"/>
    <path d="M41 220 A177 177 0 0 1 395 220" fill="none" stroke="#58585a" stroke-width="42"/>
    <circle cx="218" cy="220" r="156" fill="#fff"/>
    <text x="218" y="242" text-anchor="middle" font-family="Oswald,sans-serif" font-weight="300" font-size="56" fill="#f15a24">LENDQUAY</text>
    <g stroke-width="4" fill="#fff">
      <circle cx="67" cy="121" r="62" stroke="#f15a24"/>
      <circle cx="371" cy="121" r="62" stroke="#3d3d3f"/>
      <circle cx="74" cy="318" r="62" stroke="#3d3d3f"/>
      <circle cx="363" cy="318" r="62" stroke="#f15a24"/>
    </g>
    <g fill="none" stroke-width="2.5">
      <g stroke="#f15a24"><circle cx="67" cy="108" r="13"/><path d="M45 146 Q67 120 89 146"/><rect x="72" y="132" width="22" height="14"/></g>
      <g stroke="#3d3d3f"><rect x="352" y="102" width="38" height="30"/><line x1="346" y1="140" x2="396" y2="140"/><rect x="364" y="95" width="14" height="10"/></g>
      <g stroke="#3d3d3f"><circle cx="74" cy="318" r="10"/><circle cx="74" cy="318" r="20" stroke-dasharray="8 5"/></g>
      <g stroke="#f15a24"><circle cx="363" cy="318" r="18"/><path d="M340 300 A28 28 0 0 1 390 305"/><path d="M386 336 A28 28 0 0 1 336 331"/></g>
    </g>
    <text x="363" y="326" text-anchor="middle" font-family="Montserrat,sans-serif" font-size="22" fill="#f15a24">$</text>
  </svg>

  <div class="abs feature right" style="left:172px;top:1160px;width:198px">
    <h3 class="accent">Great rates &amp; incentives</h3>
    <p>Receive the great rates and incentives hassle-free - Lendquay does the shopping around for you.</p>
  </div>
  <div class="abs feature left" style="left:830px;top:1160px;width:198px">
    <h3>Privacy is important</h3>
    <p>Your private information is disclosed only when you follow up on representative offers from a service provider.</p>
  </div>
  <div class="abs feature right" style="left:172px;top:1355px;width:205px">
    <h3>Any time, any where</h3>
    <p>Get notifications and review representative offers wherever you are with your personal, mobile friendly Lendquay dashboard.</p>
  </div>
  <div class="abs feature left" style="left:823px;top:1355px;width:205px">
    <h3 class="accent">No fees, no obligations</h3>
    <p>The Lendquay service is free and you are under no obligation until you select the representative offer that best suits your needs.</p>
  </div>

  <div class="abs btn-solid" style="left:546px;top:1575px;width:106px;height:46px;line-height:46px;font-size:16px">Get started</div>
</section>

<!-- who -->
<section>
  <div class="abs who"></div>
  <svg class="abs who-photo" width="600" height="525" viewBox="0 0 600 525" role="img" aria-label="Photo of a smiling woman handing a card to an adviser over a desk, tinted orange">
    <defs>
      <linearGradient id="whoTint" x1="0" y1="0" x2="1" y2="1">
        <stop offset="0" stop-color="#f07a3c"/><stop offset=".5" stop-color="#c2461c"/><stop offset="1" stop-color="#6e2712"/>
      </linearGradient>
    </defs>
    <path d="M95 0 Q-20 262 95 525 L600 525 L600 0 Z" fill="#f15a24"/>
    <path d="M110 0 Q5 262 110 525 L600 525 L600 0 Z" fill="#f6f6f6"/>
    <path d="M122 0 Q20 262 122 525 L600 525 L600 0 Z" fill="url(#whoTint)"/>
  </svg>
  <h2 class="abs who-title head">Who is Lendquay?</h2>
  <p class="abs who-sub">Lendquay CEO Daniel Hartley</p>
  <p class="abs who-text">doesn't like door knockers. They have a habit of showing up during dinner, or interrupting family time. He decided there must be a better way to field offers from service providers. So now, there is.</p>
  <p class="abs who-quote">"Our goal is to get major banks, insurance companies, utility companies and other consumer service suppliers fighting for the consumer's business."</p>
  <div class="abs btn-solid" style="left:172px;top:2104px;width:106px;height:46px;line-height:46px;font-size:16px">Read more</div>
</section>

<!-- rates -->
<section>
  <h2 class="abs rates-title head">Find and compare rates</h2>

  <div class="abs tile" style="left:25px;top:2429px;background:linear-gradient(135deg,#8a8a8c,#4a4a4e)" role="img" aria-label="Photo of a couple signing a mortgage agreement">
    <svg width="80" height="80" viewBox="0 0 80 80" fill="none" stroke="#fff" stroke-width="3"><path d="M8 38 L40 10 L72 38"/><path d="M16 32 V70 H64 V32"/><circle cx="50" cy="62" r="10"/><polyline points="45,62 49,66 56,58"/></svg>
    <div class="label">Mortgage rates</div>
  </div>
  <div class="abs tile" style="left:319px;top:2429px;background:linear-gradient(135deg,#e0692e,#8a2e12)" role="img" aria-label="Photo of people reviewing personal finance paperwork, tinted orange">
    <svg width="80" height="80" viewBox="0 0 80 80" fill="none" stroke="#fff" stroke-width="3"><path d="M18 8 H48 L62 22 V72 H18 Z"/><line x1="26" y1="40" x2="40" y2="40"/><line x1="26" y1="50" x2="40" y2="50"/><line x1="26" y1="60" x2="40" y2="60"/></svg>
    <div class="label">Personal finance</div>
  </div>
  <div class="abs tile" style="left:613px;top:2429px;background:linear-gradient(135deg,#b5b2ad,#55534f)" role="img" aria-label="Photo of a woman browsing vehicles on a laptop">
    <svg width="80" height="80" viewBox="0 0 80 80" fill="none" stroke="#fff" stroke-width="3"><circle cx="40" cy="18" r="12"/><path d="M14 58 L20 40 H60 L66 58 Z"/><rect x="12" y="58" width="56" height="10"/></svg>
    <div class="label">Vehicle finance</div>
  </div>
  <div class="abs tile" style="left:906px;top:2429px;background:linear-gradient(135deg,#e25a24,#9a3516)" role="img" aria-label="Photo of a business owner reviewing asset finance, tinted orange">
    <svg width="80" height="80" viewBox="0 0 80 80" fill="none" stroke="#fff" stroke-width="3"><path d="M16 8 H50 V66 H16 Z"/><ellipse cx="60" cy="46" rx="12" ry="5"/><ellipse cx="60" cy="58" rx="12" ry="5"/><ellipse cx="60" cy="70" rx="12" ry="5"/></svg>
    <div class="label">Business &amp; asset finance</div>
  </div>

  <div class="abs tile" style="left:25px;top:2683px;background:linear-gradient(135deg,#e8703a,#8f3214)" role="img" aria-label="Photo of a family meeting an insurance adviser, tinted orange">
    <svg width="80" height="80" viewBox="0 0 80 80" fill="none" stroke="#fff" stroke-width="3"><path d="M18 8 H48 L62 22 V72 H18 Z"/><line x1="26" y1="40" x2="40" y2="40"/><line x1="26" y1="50" x2="40" y2="50"/><line x1="26" y1="60" x2="40" y2="60"/></svg>
    <div class="label">Insurance rates</div>
  </div>
  <div class="abs tile" style="left:319px;top:2683px;background:linear-gradient(135deg,#a9aaae,#4d4f55)" role="img" aria-label="Photo of banknotes changing hands beside a car">
    <svg width="80" height="80" viewBox="0 0 80 80" fill="none" stroke="#fff" stroke-width="3"><rect x="8" y="20" width="40" height="34"/><path d="M48 30 H62 L72 44 V54 H48"/><circle cx="22" cy="60" r="7"/><circle cx="60" cy="60" r="7"/></svg>
    <div class="label">Vehicle leasing</div>
  </div>
  <div class="abs tile" style="left:613px;top:2683px;background:linear-gradient(135deg,#d9622c,#7a2a10)" role="img" aria-label="Photo of a farmer standing in a field, tinted orange">
    <svg width="80" height="80" viewBox="0 0 80 80" fill="none" stroke="#fff" stroke-width="3"><rect x="22" y="10" width="26" height="24"/><rect x="10" y="34" width="60" height="16"/><circle cx="24" cy="62" r="12"/><circle cx="60" cy="64" r="8"/></svg>
    <div class="label">Farming insurance</div>
  </div>
  <div class="abs tile" style="left:906px;top:2683px;background:linear-gradient(180deg,#5a6068,#2c2f35 70%,#6a4a3a)" role="img" aria-label="Photo of an industrial gas plant under a cloudy sky">
    <svg width="80" height="80" viewBox="0 0 80 80" fill="none" stroke="#fff" stroke-width="3"><rect x="16" y="8" width="34" height="62"/><rect x="22" y="14" width="22" height="14"/><path d="M33 40 Q25 52 33 56 Q41 52 33 40 Z"/><path d="M50 30 L62 38 V62"/></svg>
    <div class="label">Power and gas</div>
  </div>
</section>

<!-- contact & footer -->
<footer>
  <div class="abs contact-band"></div>
  <svg class="abs" style="left:0;top:3036px" width="1200" height="225" viewBox="0 0 1200 225"><path d="M0 0 H1200 V160 Q600 260 0 160 Z" fill="#f15a24"/></svg>
  <div class="abs cta-row">
    <p class="cta-text head">Questions or concerns? Contact us below anytime.</p>
    <div class="cta-btn">LIVE CHAT</div>
  </div>
  <div class="abs round-btn" style="left:573px;top:3233px">
    <svg width="46" height="46" viewBox="0 0 46 46"><polyline points="14,27 23,18 32,27" fill="none" stroke="#3d3d3f" stroke-width="2.5"/></svg>
  </div>

  <div class="abs" style="left:172px;top:3364px">
    <div class="foot-h">Home</div>
    <div class="foot-links" style="margin-top:8px">About<br>Team<br>Security<br>Terms &amp; Privacy</div>
  </div>
  <div class="abs" style="left:322px;top:3364px">
    <div class="foot-h">Media</div>
    <div class="foot-links" style="margin-top:8px">NZ Ledger<br>Ledger Focus</div>
    <div class="foot-h" style="margin-top:16px">Support</div>
    <div class="foot-links" style="margin-top:8px;padding-left:3px">Help<br>Live Chat</div>
  </div>
  <div class="abs" style="left:443px;top:3364px">
    <div class="foot-h">Reach us</div>
    <div class="foot-links" style="margin-top:8px">
      <div style="display:flex;align-items:center;gap:10px">
        <svg width="17" height="17" viewBox="0 0 20 20" fill="none" stroke="#fff" stroke-width="1.5"><path d="M4 2 L8 2 L9 6 L7 8 Q9 12 12 13 L14 11 L18 12 L18 16 Q10 18 4 10 Q2 6 4 2 Z"/></svg>0508 41 63 90</div>
      <div style="display:flex;align-items:center;gap:10px;margin-top:17px">
        <svg width="17" height="13" viewBox="0 0 20 14" fill="none" stroke="#fff" stroke-width="1.5"><rect x="1" y="1" width="18" height="12"/><polyline points="1,1 10,8 19,1"/></svg>info@lendquay.co.nz</div>
      <div style="display:flex;align-items:flex-start;gap:10px;margin-top:17px;line-height:23px">
        <svg width="17" height="20" viewBox="0 0 16 20" fill="none" stroke="#fff" stroke-width="1.5" style="margin-top:4px"><path d="M8 19 Q1 11 1 7 A7 7 0 0 1 15 7 Q15 11 8 19 Z"/><circle cx="8" cy="7" r="2.5"/></svg>
        <span>14 Kestrel Lane, Auckland<br>1010, New Zealand</span></div>
    </div>
  </div>
  <div class="abs foot-h" style="left:667px;top:3364px">Contact us</div>
  <div class="abs field" style="left:667px;top:3413px;width:176px;height:46px">Name</div>
  <div class="abs field" style="left:850px;top:3413px;width:176px;height:46px">Email</div>
  <div class="abs field" style="left:667px;top:3473px;width:359px;height:46px">Number</div>
  <div class="abs btn-solid" style="left:667px;top:3532px;width:111px;height:46px;line-height:46px;font-size:18px;font-weight:400">Submit</div>

  <div class="abs rule"></div>
  <p class="abs copy head">Copyrights @ 2020 Lendquay. All rights reserved.</p>
  <p class="abs head light" style="left:1078px;top:3688px;font-size:16px;color:#fff">C20</p>
</footer>

</body>
</html>
```